Business Card Design Project

Lorabelle is a women fashion house focusing on youthful glamour.

We bring together unique designs, premium quality materials and top craftsmanship to deliver sophisticated yet playful glamour, fun and excitement to the confident woman.

We can sum up the brand identity in 3 words:
Glamour – Sophistication – Unique

Industry/Entity Type

Fashion

Requirements
Must have
• Nim Ferrasco
nim.ferrasco@lorabelle-example.com
Mobile: 081 536 2947
Instragram: lorabelle_label
Facebook: lorabelle

Creative Director
Lorabelle Co., LTD
TEL: 02 631 48 97
42 Maple Row, 2nd Floor , D Building , Thonrak , Chaloemrat 28.
East Sanphet , Rattana , Bangkok 10240 Thailand
www.lorabelle-example.com

```html
<!DOCTYPE html>
<html lang="en">
<head>
<meta charset="utf-8">
<title>Lorabelle — Business Card</title>
<link rel="stylesheet" href="https://fonts.googleapis.com/css2?family=Roboto+Condensed:wght@300;400&display=swap">
<style>
  :root {
    --page-bg: #e9e7e4;
    --card-top: #ffffff;
    --card-bottom: #ececec;
    --brand-ink: #454545;
    --name-ink: #5a5a5a;
    --text-ink: #777777;
    --icon-ink: #555555;
  }
  html, body {
    margin: 0;
    width: 1200px;
    height: 1000px;
    overflow: hidden;
    background: var(--page-bg);
  }
  .card {
    position: absolute;
    left: 180px;
    top: 260px;
    width: 840px;
    height: 480px;
    background: linear-gradient(160deg, var(--card-top) 35%, var(--card-bottom) 100%);
    box-shadow: 0 6px 20px rgba(0,0,0,0.12);
    font-family: "Roboto Condensed", "Arial Narrow", sans-serif;
    font-weight: 300;
    color: var(--text-ink);
  }
  .brand {
    position: absolute;
    right: 48px;
    top: 40px;
    margin: 0;
    font-family: "Roboto Condensed", "Arial Narrow", sans-serif;
    font-weight: 300;
    font-size: 60px;
    line-height: 1;
    color: var(--brand-ink);
  }
  .person {
    position: absolute;
    left: 44px;
    top: 138px;
  }
  .person-name {
    margin: 0;
    font-size: 26px;
    font-weight: 400;
    color: var(--name-ink);
  }
  .person-title {
    margin: 2px 0 0;
    font-size: 16px;
    color: var(--text-ink);
  }
  .contacts {
    position: absolute;
    left: 44px;
    top: 218px;
    margin: 0;
    padding: 0;
    list-style: none;
    font-size: 16px;
  }
  .contact {
    display: flex;
    align-items: center;
    height: 26px;
  }
  .contact-icon {
    width: 14px;
    height: 14px;
    margin-right: 12px;
    flex: none;
  }
  .contact-dot {
    width: 11px;
    height: 11px;
    margin: 0 13px 0 1px;
    background: var(--icon-ink);
    border-radius: 50%;
    flex: none;
  }
  .address {
    position: absolute;
    left: 44px;
    bottom: 36px;
    display: flex;
    align-items: flex-start;
    font-size: 17px;
    line-height: 26px;
  }
  .address p { margin: 0; }
</style>
</head>
<body>
  <section class="card" aria-label="Lorabelle business card, front">
    <h1 class="brand">Lorabelle</h1>

    <div class="person">
      <p class="person-name">Nim Ferrasco</p>
      <p class="person-title">Creative Director</p>
    </div>

    <ul class="contacts">
      <li class="contact">
        <svg class="contact-icon" viewBox="0 0 14 14" aria-label="Email"><rect x="1" y="3" width="12" height="9" fill="var(--icon-ink)"/><path d="M1 3 L7 8 L13 3" stroke="#fff" stroke-width="1.2" fill="none"/></svg>
        <span>nim.ferrasco@lorabelle-example.com</span>
      </li>
      <li class="contact">
        <svg class="contact-icon" viewBox="0 0 14 14" aria-label="Mobile"><rect x="3.5" y="1" width="7" height="12" rx="1" fill="none" stroke="var(--icon-ink)" stroke-width="1.5"/><rect x="5" y="10.5" width="4" height="1" fill="var(--icon-ink)"/></svg>
        <span>081 536 2947</span>
      </li>
      <li class="contact">
        <svg class="contact-icon" viewBox="0 0 14 14" aria-label="Telephone"><path d="M3 1.5 L5.5 4 L4.3 5.8 Q5.5 8.5 8.2 9.7 L10 8.5 L12.5 11 L11 12.8 Q6 12.5 2.5 8 Q1 5 1.3 3 Z" fill="var(--icon-ink)"/></svg>
        <span>02 631 48 97</span>
      </li>
      <li class="contact">
        <span class="contact-dot" aria-hidden="true"></span>
        <span>lorabelle_label</span>
      </li>
      <li class="contact">
        <svg class="contact-icon" viewBox="0 0 14 14" aria-label="Website"><circle cx="7" cy="7" r="5.8" fill="none" stroke="var(--icon-ink)" stroke-width="1.3"/><ellipse cx="7" cy="7" rx="2.5" ry="5.8" fill="none" stroke="var(--icon-ink)" stroke-width="1"/><path d="M1.2 7 H12.8 M2 4.2 H12 M2 9.8 H12" stroke="var(--icon-ink)" stroke-width="0.9"/></svg>
        <span>www.lorabelle-example.com</span>
      </li>
      <li class="contact">
        <span class="contact-dot" aria-hidden="true"></span>
        <span>lorabelle</span>
      </li>
    </ul>

    <div class="address">
      <svg class="contact-icon" viewBox="0 0 14 14" aria-label="Address" style="margin-top:6px"><path d="M7 13 L3 7.2 A4.6 4.6 0 1 1 11 7.2 Z" fill="var(--icon-ink)"/><circle cx="7" cy="4.8" r="1.6" fill="#fff"/></svg>
      <div>
        <p>42 Maple Row, 2nd Floor , D Building , Thonrak , Chaloemrat 28. East Sanphet ,</p>
        <p>Rattana , Bangkok 10240 Thailand</p>
      </div>
    </div>
  </section>
</body>
</html>
```